Vantiqo custom business card design

Need a authentic, innovative business card design for a new mobile app business. I am uploading a few screen images from our app for you to view. I would like app design theme to match business card design. I can also send logo images.

```html
<!DOCTYPE html>
<html lang="en">
<head>
<meta charset="utf-8">
<title>Vantiqo Business Card</title>
<link href="https://fonts.googleapis.com/css2?family=Open+Sans:wght@400;600;800&display=swap" rel="stylesheet">
<style>
  :root {
    --stage: #d9d6d3;
    --card: #1f2022;
    --card-edge: #141516;
    --ink: #ffffff;
    --muted: #b9b9bd;
    --accent: #6a1fa6;
    --emboss: #2c2d30;
  }
  * { margin: 0; padding: 0; box-sizing: border-box; }
  html, body { width: 1200px; height: 864px; overflow: hidden; }
  body {
    background: var(--stage);
    font-family: "Open Sans", Arial, sans-serif;
    position: relative;
  }
  .card {
    position: absolute;
    width: 540px;
    height: 309px;
    background: var(--card);
    border-radius: 4px;
    box-shadow: 0 10px 24px rgba(0,0,0,0.28);
    overflow: hidden;
  }
  .card--front { left: 40px; top: 278px; }
  .card--back { left: 620px; top: 278px; }

  /* front side */
  .front-mark {
    position: absolute;
    left: 0; right: 0; top: 98px;
    display: flex; align-items: center; justify-content: center; gap: 12px;
  }
  .front-mark__dot {
    width: 26px; height: 26px; border-radius: 50%;
    background: var(--emboss);
  }
  .front-mark__name {
    font-weight: 800; font-size: 44px; color: var(--emboss);
    letter-spacing: 0.5px;
  }
  .front-url {
    position: absolute; left: 0; right: 0; bottom: 52px;
    text-align: center; color: var(--muted);
    font-size: 13px; letter-spacing: 7px;
  }

  /* back side */
  .person { position: absolute; left: 30px; top: 48px; }
  .person__name {
    color: var(--accent); font-weight: 600; font-size: 18px;
    letter-spacing: 0.5px; line-height: 1;
  }
  .person__title {
    color: var(--ink); font-size: 12px; margin-top: 4px; letter-spacing: 0.4px;
  }
  .contact { position: absolute; left: 30px; top: 98px; list-style: none; }
  .contact li {
    display: flex; align-items: center; gap: 10px;
    color: var(--ink); font-size: 13px; line-height: 19px;
  }
  .contact svg { width: 12px; height: 12px; fill: var(--accent); flex: none; }
  .divider { position: absolute; height: 1.5px; background: var(--ink); }
  .divider--top { left: 30px; width: 360px; top: 180px; }
  .divider--bottom { left: 300px; width: 210px; top: 222px; }

  .brand {
    position: absolute; right: 30px; top: 96px;
    display: flex; align-items: center; gap: 10px;
  }
  .brand__dot { width: 22px; height: 22px; border-radius: 50%; background: var(--accent); }
  .brand__name { font-weight: 800; font-size: 32px; color: var(--ink); }

  .address {
    position: absolute; right: 30px; top: 234px;
    text-align: right; color: var(--ink); font-size: 13px; line-height: 19px;
  }
</style>
</head>
<body>

<section class="card card--front" aria-label="Card front">
  <div class="front-mark">
    <span class="front-mark__dot"></span>
    <span class="front-mark__name">Vantiqo</span>
  </div>
  <p class="front-url">www.vantiqo.com</p>
</section>

<section class="card card--back" aria-label="Card back">
  <div class="person">
    <p class="person__name">MARA LENZ</p>
    <p class="person__title">PRESIDENT</p>
  </div>

  <ul class="contact">
    <li>
      <svg viewBox="0 0 12 12" aria-hidden="true"><path d="M2.5 1l2 2.4-1.1 1.3c.8 1.6 2 2.8 3.6 3.6l1.3-1.1L11 9.3 9.8 11C5 10.7 1.3 7 1 2.2z"/></svg>
      555 0142 7781
    </li>
    <li>
      <svg viewBox="0 0 12 12" aria-hidden="true"><path d="M3.5 0h5a1 1 0 0 1 1 1v10a1 1 0 0 1-1 1h-5a1 1 0 0 1-1-1V1a1 1 0 0 1 1-1zm.5 1.5v7.5h4V1.5zM6 9.8a.7.7 0 1 0 0 1.4.7.7 0 0 0 0-1.4z"/></svg>
      555 0198 3364
    </li>
    <li>
      <svg viewBox="0 0 12 12" aria-hidden="true"><path d="M3 0h5v3H3zM1 4h10v6H9v2H3v-2H1zm3 4v3h4V8z"/></svg>
      555 0176 2209
    </li>
    <li>
      <svg viewBox="0 0 12 12" aria-hidden="true"><path d="M0 2h12v1.2L6 7 0 3.2zm0 2.6L6 8.4l6-3.8V10H0z"/></svg>
      mara@vantiqo.com
    </li>
  </ul>

  <div class="divider divider--top"></div>

  <div class="brand">
    <span class="brand__dot"></span>
    <span class="brand__name">Vantiqo</span>
  </div>

  <div class="divider divider--bottom"></div>

  <address class="address" style="font-style:normal">
    4120 Harbor Crest Lane<br>
    Glen Oaks, NY 11004<br>
    www.vantiqo.com
  </address>
</section>

</body>
</html>
```